Coastline Premier Retreats Business Card Design

Design a business card for Coastline Premier Retreats. Look at the website for colors and reference. Card should have logo, name, title, office number, mobile number, email, URL and a tagline like, "Luxury Hotel & Resort Email Marketing" (This might change).

https://www.coastlinepremierretreats.example

The rest I will leave up to your imagination.

Contact Information for Business Card

Logo, name, title, office number, mobile number, email, URL and a tagline like, "Luxury Hotel & Resort Email Marketing" (This might change).

```html
<!DOCTYPE html>
<html lang="en">
<head>
<meta charset="utf-8">
<title>Coastline Premier Retreats – Business Card</title>
<link rel="stylesheet" href="https://fonts.googleapis.com/css2?family=Open+Sans:wght@400;600;700;800&display=swap">
<style>
  :root {
    --backdrop: #222222;
    --card-dark: #1d1d20;
    --card-layer-1: #222226;
    --card-layer-2: #27272b;
    --accent: #f07622;
    --text-light: #ffffff;
    --text-muted: #d9d9dc;
    --ink: #111111;
    --sky: #b9cfe6;
    --sea: #7fb8b4;
    --foliage: #8a9a63;
  }
  * { box-sizing: border-box; margin: 0; padding: 0; }
  html, body {
    width: 1200px; height: 780px; overflow: hidden;
    background: var(--backdrop);
    font-family: "Open Sans", Arial, sans-serif;
  }
  .canvas {
    position: relative; width: 1200px; height: 780px;
  }
  .card {
    position: absolute; top: 90px;
    width: 360px; height: 600px;
    border-radius: 26px; overflow: hidden;
    box-shadow: 0 18px 40px rgba(0,0,0,.55);
  }

  /* Front */
  .card--front { left: 190px; }
  .front__photo {
    position: absolute; inset: 0;
    background: linear-gradient(90deg, var(--sky) 0%, #c8d7e3 22%, var(--foliage) 40%, var(--sea) 58%, #9fb07a 78%, var(--foliage) 100%);
    opacity: .9;
  }
  .front__brand {
    position: absolute; left: 50%; top: 50%;
    transform: translate(-50%, -50%) rotate(-90deg);
    display: flex; align-items: center; gap: 14px;
    white-space: nowrap;
  }
  .front__brand-mark {
    width: 22px; height: 22px; background: var(--accent);
  }
  .front__brand-name {
    font-weight: 800; font-size: 34px; letter-spacing: 1px;
    color: var(--ink); text-transform: uppercase; line-height: 1;
  }

  /* Back */
  .card--back { left: 650px; background: var(--card-dark); }
  .back__waves { position: absolute; inset: 0; }
  .back__brand {
    position: absolute; top: 58px; left: 0; right: 0;
    display: flex; align-items: center; justify-content: center; gap: 10px;
  }
  .back__brand-mark { width: 14px; height: 14px; background: var(--accent); }
  .back__brand-name {
    font-weight: 800; font-size: 17px; letter-spacing: .5px;
    color: var(--text-light); text-transform: uppercase;
  }
  .back__person {
    position: absolute; top: 180px; left: 0; right: 0; text-align: center;
  }
  .person__name { font-weight: 800; font-size: 30px; line-height: 1.1; }
  .person__first { color: var(--accent); }
  .person__last { color: var(--text-light); }
  .person__title {
    margin-top: 4px; font-weight: 600; font-size: 14px; color: var(--text-light);
  }
  .contact__icons {
    display: flex; justify-content: center; gap: 10px; margin-top: 16px;
  }
  .contact__icon {
    width: 24px; height: 24px; border-radius: 50%;
    background: var(--accent); display: flex; align-items: center; justify-content: center;
  }
  .contact__list {
    list-style: none; margin-top: 14px;
    font-size: 12.5px; line-height: 1.55; color: var(--text-muted);
  }
  .back__tagline {
    position: absolute; bottom: 56px; left: 0; right: 0; text-align: center;
    color: var(--accent); font-weight: 600; font-size: 15px; line-height: 1.35;
  }
</style>
</head>
<body>
<main class="canvas">

  <section class="card card--front" aria-label="Business card front">
    <div class="front__photo" role="img" aria-label="Photograph of a rocky coastline with pine trees and turquoise sea under a pale sky"></div>
    <div class="front__brand">
      <span class="front__brand-mark"></span>
      <span class="front__brand-name">Coastline Premier Retreats</span>
    </div>
  </section>

  <section class="card card--back" aria-label="Business card back">
    <svg class="back__waves" viewBox="0 0 360 600" preserveAspectRatio="none" aria-hidden="true">
      <path d="M0 470 Q 180 560 360 420 L360 600 L0 600 Z" fill="var(--card-layer-2)"/>
      <path d="M0 440 Q 200 520 360 360 L360 600 L0 600 Z" fill="var(--card-layer-1)" opacity=".9"/>
      <path d="M0 440 Q 200 520 360 360" fill="none" stroke="#141416" stroke-width="3" opacity=".6"/>
      <path d="M0 470 Q 180 560 360 420" fill="none" stroke="#141416" stroke-width="3" opacity=".5"/>
    </svg>

    <div class="back__brand">
      <span class="back__brand-mark"></span>
      <span class="back__brand-name">Coastline Premier Retreats</span>
    </div>

    <div class="back__person">
      <h1 class="person__name"><span class="person__first">Marta</span> <span class="person__last">Vollen</span></h1>
      <p class="person__title">Co-Founder</p>

      <div class="contact__icons">
        <span class="contact__icon" aria-label="Office phone">
          <svg width="12" height="12" viewBox="0 0 24 24"><path d="M6.6 10.8a15 15 0 0 0 6.6 6.6l2.2-2.2a1 1 0 0 1 1-.25 11.4 11.4 0 0 0 3.6.6 1 1 0 0 1 1 1V20a1 1 0 0 1-1 1A17 17 0 0 1 3 4a1 1 0 0 1 1-1h3.5a1 1 0 0 1 1 1 11.4 11.4 0 0 0 .6 3.6 1 1 0 0 1-.25 1z" fill="#fff"/></svg>
        </span>
        <span class="contact__icon" aria-label="Mobile">
          <svg width="12" height="12" viewBox="0 0 24 24"><rect x="7" y="2" width="10" height="20" rx="2" fill="none" stroke="#fff" stroke-width="2"/><circle cx="12" cy="18" r="1.2" fill="#fff"/></svg>
        </span>
        <span class="contact__icon" aria-label="Email">
          <svg width="12" height="12" viewBox="0 0 24 24"><rect x="3" y="5" width="18" height="14" rx="1.5" fill="none" stroke="#fff" stroke-width="2"/><path d="M3 6l9 7 9-7" fill="none" stroke="#fff" stroke-width="2"/></svg>
        </span>
        <span class="contact__icon" aria-label="Website">
          <svg width="12" height="12" viewBox="0 0 24 24"><circle cx="12" cy="12" r="9" fill="none" stroke="#fff" stroke-width="2"/><path d="M3 12h18M12 3c3 3 3 15 0 18M12 3c-3 3-3 15 0 18" fill="none" stroke="#fff" stroke-width="1.6"/></svg>
        </span>
      </div>

      <ul class="contact__list">
        <li>(555) 310-4826</li>
        <li>(555) 310-9071</li>
        <li>www.coastlinepremierretreats.example</li>
        <li>info@coastlinepremierretreats.example</li>
      </ul>
    </div>

    <p class="back__tagline">Luxury Hotel &amp;<br>Resort Email Marketing</p>
  </section>

</main>
</body>
</html>
```